Business card for Eyelash extension salon in Crestmoor Hills,California USA

We need new business card for our salon in Crestmoor Hills. The salon name is 'Lashvera' . We would like to have...Business name: Lashvera Name of person: will provide later Address 4720 N.Alder Crest Ave Crestmoor Hills , CA 90210 Phone: will provide later (Text only) Web: www.lashverastudio.example Snapgrid icon, Circlebook icon follow us for seasonal campaign and news @lashverastudiolounge Design should look elegant, high-end, clean, simple, cohesive with my brand. Please refer my brand board. Business name color will be metallic bronzy color. Im thinking grey background or white background. Thanks

Target Market(s)

25-35. Gender neutral. People who are in Entertainment business industry.
This is High-end Eyelash extension salon in Crestmoor Hills

Industry/Entity Type

Beauty Salon

Contact Information for Business Card

Business name: Lashvera
Name of person: will provide later
Address 4720 N.Alder Crest Ave Crestmoor Hills , CA 90210
Phone: will provide later (Text only)
Web: www.lashverastudio.example
Snapgrid icon, Circlebook icon
follow us for seasonal campaign and news @lashverastudiolounge

Requirements
Must have
• Beautiful, elegant, clean and simple look but very attractive and modern
Should not have
• We don't like too clutter, too busy designs.

```html
<!DOCTYPE html>
<html lang="en">
<head>
<meta charset="utf-8">
<title>Lashvera Crestmoor Hills – Business Card</title>
<link rel="stylesheet" href="https://fonts.googleapis.com/css2?family=Playfair+Display:wght@400;600&family=Josefin+Sans:wght@400&display=swap">
<style>
  :root {
    --bronze: #8a6a4f;
    --backdrop: #e4e4e4;
    --marble-light: #f1f1f1;
    --marble-mid: #d6d6d6;
    --marble-dark: #b9b9b9;
    --card-text: #ffffff;
  }
  * { margin: 0; padding: 0; box-sizing: border-box; }
  html, body {
    width: 1200px; height: 960px; overflow: hidden;
    background: var(--backdrop);
  }
  .canvas { position: relative; width: 1200px; height: 960px; }

  .card { position: absolute; width: 600px; height: 342px; }
  .card--front { left: 302px; top: 123px; background: var(--bronze); }
  .card--back  { left: 299px; top: 496px; }

  .marble {
    position: absolute;
    background:
      radial-gradient(ellipse at 30% 20%, var(--marble-light) 0%, transparent 55%),
      radial-gradient(ellipse at 75% 80%, var(--marble-mid) 0%, transparent 60%),
      linear-gradient(135deg, var(--marble-mid) 0%, var(--marble-light) 45%, var(--marble-dark) 100%);
  }
  .card--front .marble { left: 14px; top: 12px; right: 15px; bottom: 16px; }
  .card--back .marble { inset: 0; }

  .brand {
    position: absolute; left: 0; right: 0; top: 110px;
    text-align: center;
    font-family: "Playfair Display", serif; font-weight: 400;
    font-size: 88px; line-height: 1; color: var(--bronze);
  }
  .brand-location {
    position: absolute; left: 291px; top: 232px;
    font-family: "Josefin Sans", sans-serif; font-size: 11.5px;
    letter-spacing: 2.2px; color: var(--bronze);
  }

  .details {
    position: absolute; left: 14px; top: 12px; width: 571px; height: 313px;
    background: var(--bronze); color: var(--card-text);
    font-family: "Playfair Display", serif; text-align: center;
    font-variant-numeric: lining-nums;
    padding-top: 62px;
  }
  .person-name { font-weight: 600; font-size: 21px; letter-spacing: 0.5px; line-height: 1.1; }
  .person-role { font-weight: 600; font-size: 14.5px; letter-spacing: 0.3px; line-height: 1.2; }
  .address { margin-top: 10px; font-size: 14px; line-height: 1.35; }
  .contact { margin-top: 8px; font-size: 14px; line-height: 1.38; }
  .social { margin-top: 14px; font-size: 12px; letter-spacing: 0.5px; }
</style>
</head>
<body>
<main class="canvas">
  <section class="card card--front">
    <div class="marble" role="img" aria-label="White and grey marble texture background"></div>
    <div class="brand">Lashvera</div>
    <div class="brand-location">CRESTMOOR HILLS</div>
  </section>

  <section class="card card--back">
    <div class="marble" role="img" aria-label="White and grey marble texture border"></div>
    <div class="details">
      <p class="person-name">ADRIAN VALE</p>
      <p class="person-role">CEO/FOUNDER</p>
      <p class="address">4720 N.Alder Crest Ave<br>Crestmoor Hills, CA 90417</p>
      <p class="contact">555 014 2290<br>news@lashverastudiolounge<br>lashverastudio.example</p>
      <p class="social">Circlebook &nbsp;·&nbsp; Snapgrid</p>
    </div>
  </section>
</main>
</body>
</html>
```